design a construction company business card

Design business card around our logo. Card must have all the typical info: name, title, address, phone, email, business name, etc. Somewhere on the card I would like to see our motto "Built on integrity... Inspired by commitment." Consider adding a splash of bright orange to the card to complement the blues and silvers/grays in the logo. We are open to metallic inks, textures, etc. We would like to see options on both light and dark backgrounds. The font in the logo is Euro Technic Extended Regular.

```html
<!DOCTYPE html>
<html lang="en">
<head>
<meta charset="utf-8">
<title>Harlow Building Co. – Business Card</title>
<link href="https://fonts.googleapis.com/css2?family=Roboto:ital,wght@0,400;0,700;1,400&display=swap" rel="stylesheet">
<style>
  :root {
    --page-bg: #3a3a3a;
    --blue-deep: #24399a;
    --blue-bright: #1f74bb;
    --blue-ink: #1f3f9c;
    --silver: #c3c6cc;
    --grey-text: #3d3d3d;
    --grey-swoosh: #8e9095;
    --orange: #f7931e;
    --white: #ffffff;
  }
  * { margin: 0; padding: 0; box-sizing: border-box; }
  html, body {
    width: 1200px; height: 960px; overflow: hidden;
    background: var(--page-bg);
    font-family: "Roboto", Arial, sans-serif;
  }
  .canvas {
    width: 1200px; height: 960px;
    display: flex; flex-direction: column; align-items: center; justify-content: center;
    gap: 40px;
  }
  .card {
    position: relative;
    width: 700px; height: 400px;
    border-radius: 4px;
    overflow: hidden;
    box-shadow: 0 10px 30px rgba(0,0,0,0.45);
  }

  /* Front side */
  .card-front {
    background: linear-gradient(120deg, var(--blue-deep) 0%, var(--blue-bright) 100%);
    display: flex; flex-direction: column; align-items: center; justify-content: center;
  }
  .front-brand {
    display: flex; align-items: center; gap: 14px;
    color: var(--silver);
    font-weight: 700; font-size: 40px; letter-spacing: 3px;
    text-transform: uppercase;
  }
  .front-brand .brand-square { width: 30px; height: 30px; background: var(--silver); }
  .accent-rule {
    width: 90px; height: 4px; background: var(--orange);
    margin: 22px 0 16px;
  }
  .motto {
    color: var(--white); font-size: 17px; font-style: italic; letter-spacing: 0.5px;
  }

  /* Back side */
  .card-back { background: linear-gradient(180deg, #ffffff 0%, #f3f3f3 100%); }
  .back-brand {
    position: absolute; left: 60px; top: 58px;
    display: flex; align-items: center; gap: 10px;
    color: var(--blue-ink);
    font-weight: 700; font-size: 26px; letter-spacing: 1.5px;
    text-transform: uppercase;
  }
  .back-brand .brand-square { width: 20px; height: 20px; background: var(--blue-ink); }

  .contact {
    position: absolute; left: 60px; top: 150px;
    color: var(--grey-text); font-size: 17px; line-height: 24px;
  }
  .contact .address { margin-bottom: 18px; }
  .contact-list { list-style: none; }
  .contact-list li { display: flex; align-items: center; gap: 10px; }
  .contact-list svg { width: 16px; height: 16px; fill: var(--blue-ink); flex: none; }

  .person {
    position: absolute; right: 60px; top: 140px; text-align: right;
  }
  .person .name { color: var(--blue-ink); font-weight: 700; font-size: 31px; }
  .person .title { color: var(--grey-text); font-size: 18px; margin-top: 2px; }
  .person .title-rule {
    display: block; width: 48px; height: 3px; background: var(--orange);
    margin: 10px 0 0 auto;
  }

  .swoosh { position: absolute; left: 0; bottom: 0; width: 700px; height: 400px; }
  .web {
    position: absolute; right: 40px; bottom: 16px;
    color: var(--white); font-size: 18px; letter-spacing: 0.5px;
  }
</style>
</head>
<body>
<main class="canvas">
  <section class="card card-front" aria-label="Card front">
    <div class="front-brand"><span class="brand-square"></span>Harlow Building Co.</div>
    <span class="accent-rule"></span>
    <p class="motto">Built on integrity... Inspired by commitment.</p>
  </section>

  <section class="card card-back" aria-label="Card back">
    <svg class="swoosh" viewBox="0 0 700 400" aria-hidden="true">
      <defs>
        <linearGradient id="bandGrad" x1="0" x2="1" y1="0" y2="0">
          <stop offset="0" stop-color="#1f74bb"/>
          <stop offset="1" stop-color="#24399a"/>
        </linearGradient>
      </defs>
      <path d="M0,338 Q380,312 700,346 L700,352 Q380,324 0,346 Z" fill="var(--grey-swoosh)"/>
      <path d="M100,400 Q380,330 700,346 L700,350 Q380,336 110,400 Z" fill="var(--orange)"/>
      <path d="M110,400 Q380,336 700,352 L700,400 Z" fill="url(#bandGrad)"/>
    </svg>

    <div class="back-brand"><span class="brand-square"></span>Harlow Building Co.</div>

    <div class="contact">
      <p class="address">Level 2, 17 Carden Lane<br>Ashford, VIC 3010</p>
      <ul class="contact-list">
        <li><svg viewBox="0 0 24 24"><path d="M6.6 10.8a15 15 0 0 0 6.6 6.6l2.2-2.2c.3-.3.7-.4 1-.2 1.1.4 2.3.6 3.6.6.6 0 1 .4 1 1V20c0 .6-.4 1-1 1A17 17 0 0 1 3 4c0-.6.4-1 1-1h3.5c.6 0 1 .4 1 1 0 1.3.2 2.5.6 3.6.1.3 0 .7-.2 1z"/></svg>555 010 4821</li>
        <li><svg viewBox="0 0 24 24"><path d="M7 1h10a2 2 0 0 1 2 2v18a2 2 0 0 1-2 2H7a2 2 0 0 1-2-2V3a2 2 0 0 1 2-2zm0 3v14h10V4z"/></svg>555 019 3376</li>
        <li><svg viewBox="0 0 24 24"><path d="M2 5h20v14H2zm2 2v.5l8 5 8-5V7z"/></svg>info@harlowbuild.com</li>
      </ul>
    </div>

    <div class="person">
      <p class="name">Daniel Reyes</p>
      <p class="title">Director</p>
      <span class="title-rule"></span>
    </div>

    <p class="web">www.harlowbuild.com</p>
  </section>
</main>
</body>
</html>
```